Business Card design for law firm = Brightvale Australia

We are seeking a new design for our business cards.
We are keeping our logo, which is attached.
We need space for
Name
Title
Address is , which is
Level 7
214 Marlowe Street
Sydney NSW 2047
Phone :
Mobile :
Fax :
Email :
DX :
website www.brightvale-example.com.au

Industry/Entity Type

Law Firm / Banking and Finance

Contact Information for Business Card

We are seeking a new design for our business cards. We are keeping our logo. We need space for Name Title Address is Level 7 214 Marlowe Street Sydney NSW 2047 Phone Mobile Fax Email DX website www.brightvale-example.com.au

Colors
0054AA
0677BA
7BADD7
CADEEF
E8F1F8

Requirements
Must have
• see our website for general feel www.brightvale-example.com.au

```html
<!DOCTYPE html>
<html lang="en">
<head>
<meta charset="utf-8">
<title>Brightvale Australia – Business Card</title>
<link rel="stylesheet" href="https://fonts.googleapis.com/css2?family=Arimo:wght@400;700&family=Tinos&display=swap">
<style>
  :root {
    --bg: #1f1f21;
    --card: #0c0c0d;
    --card-edge: #19191a;
    --blue-deep: #0677BA;
    --blue-bright: #1a9ad6;
    --white: #f4f4f4;
    --silver: #d6d6d6;
    --divider: #4a4a4c;
  }
  * { box-sizing: border-box; margin: 0; padding: 0; }
  html, body {
    width: 1200px; height: 900px; overflow: hidden;
    background: var(--bg);
  }
  .canvas {
    width: 1200px; height: 900px;
    display: flex; flex-direction: column;
    align-items: center; justify-content: center; gap: 24px;
  }
  .card {
    position: relative;
    width: 700px; height: 400px;
    background: var(--card);
    border: 1px solid var(--card-edge);
    border-radius: 26px;
    overflow: hidden;
  }

  /* Front: contact side */
  .brand {
    position: absolute; left: 40px; top: 0; width: 292px; height: 400px;
    display: flex; align-items: center; justify-content: center;
  }
  .brand-name {
    font-family: "Arimo", Arial, sans-serif;
    font-weight: 400;
    font-size: 40px; line-height: 1;
    color: var(--blue-deep);
  }
  .divider {
    position: absolute; left: 352px; top: 70px;
    width: 1px; height: 270px;
    background: var(--divider);
  }
  .contact {
    position: absolute; left: 382px; top: 58px; right: 20px;
    font-family: "Arimo", Arial, sans-serif;
    color: var(--white);
  }
  .person-name {
    font-family: "Tinos", "Times New Roman", serif;
    font-size: 32px; line-height: 1;
    color: var(--blue-deep);
  }
  .person-title {
    font-size: 17px; color: var(--blue-bright);
    margin-top: 2px; margin-bottom: 16px;
  }
  .contact-list { list-style: none; }
  .contact-item {
    display: flex; align-items: center; gap: 8px;
    font-size: 15px; line-height: 1; height: 24px;
    white-space: nowrap;
  }
  .contact-icon {
    width: 18px; height: 18px; flex: none;
    background: var(--blue-deep);
    display: flex; align-items: center; justify-content: center;
  }
  .contact-icon svg { width: 12px; height: 12px; }
  .accent { color: var(--blue-bright); }
  .address {
    font-style: normal; font-size: 16px; line-height: 1.35;
    margin-top: 18px; margin-left: 26px;
  }

  /* Back: brand side */
  .back-brand {
    position: absolute; left: 0; right: 0; top: 148px;
    text-align: center;
  }
  .back-brand .brand-name { color: var(--silver); font-size: 52px; }
  .dx {
    position: absolute; left: 0; right: 0; top: 262px;
    text-align: center;
    font-family: "Arimo", Arial, sans-serif;
    font-size: 18px; color: var(--white);
  }
  .dx-label { color: var(--blue-deep); }
</style>
</head>
<body>
<main class="canvas">

  <section class="card card-front" aria-label="Business card, contact side">
    <div class="brand">
      <span class="brand-name">Brightvale</span>
    </div>

    <div class="divider"></div>

    <div class="contact">
      <p class="person-name">Daniel Hartley</p>
      <p class="person-title">Managing Director</p>
      <ul class="contact-list">
        <li class="contact-item">
          <span class="contact-icon"><svg viewBox="0 0 12 12"><path d="M2 1h2.5l1 2.5-1.5 1a6 6 0 0 0 3.5 3.5l1-1.5 2.5 1V11C5 11 1 7 1 2z" fill="#fff"/></svg></span>
          044-555 010 201
        </li>
        <li class="contact-item">
          <span class="contact-icon"><svg viewBox="0 0 12 12"><rect x="3" y="0.5" width="6" height="11" rx="1" fill="none" stroke="#fff"/><circle cx="6" cy="9.5" r="0.7" fill="#fff"/></svg></span>
          044-555 010 202
        </li>
        <li class="contact-item">
          <span class="contact-icon"><svg viewBox="0 0 12 12"><rect x="3" y="1" width="6" height="3" fill="none" stroke="#fff"/><rect x="1" y="4" width="10" height="5" fill="#fff"/><rect x="3" y="8" width="6" height="3" fill="#0677BA" stroke="#fff"/></svg></span>
          044-555 010 203
        </li>
        <li class="contact-item">
          <span class="contact-icon"><svg viewBox="0 0 12 12"><rect x="1" y="2.5" width="10" height="7" fill="none" stroke="#fff"/><path d="M1 2.5l5 4 5-4" fill="none" stroke="#fff"/></svg></span>
          info@brightvale-example.com.au
        </li>
        <li class="contact-item">
          <span class="contact-icon"><svg viewBox="0 0 12 12"><circle cx="6" cy="6" r="5" fill="none" stroke="#fff"/><ellipse cx="6" cy="6" rx="2.2" ry="5" fill="none" stroke="#fff"/><path d="M1 6h10" stroke="#fff"/></svg></span>
          <span>www.<span class="accent">brightvale-example</span>.com.au</span>
        </li>
      </ul>
      <address class="address">
        Level 7, 214 Marlowe Street<br>
        Sydney NSW 2047
      </address>
    </div>
  </section>

  <section class="card card-back" aria-label="Business card, brand side">
    <div class="back-brand">
      <span class="brand-name">Brightvale</span>
    </div>
    <p class="dx"><span class="dx-label">DX :</span>555010299</p>
  </section>

</main>
</body>
</html>
```